Business Card Design

I'm a commercial general contractor remodel offices, hotels, health clubs and stores mostly San Francisco and the peninsula
the file I down loaded is kind of what I want I like the I beam with my company name in it, that would be fine with me but if you have better Idea will look at it you never know, I'm decided to give in and change my company name to how every one knows me, I have been in business since 1991, I like the I beam logo I included one of my old card from my old company for reference for you.

BROCK CONSTRUCTION (is my company name)
Warren Pelkey contractor, LIc 514387
3148 Larkspur Row, San Bruno, California 94071
mobile, (415) 736-4052
phone (650) 514-2087
Fax, (650) 514-2088
email, brock@brockconstruction.example

```html
<!DOCTYPE html>
<html lang="en">
<head>
<meta charset="utf-8">
<title>Brock Construction – Business Card</title>
<link href="https://fonts.googleapis.com/css2?family=Source+Sans+3:wght@400;600&display=swap" rel="stylesheet">
<style>
  :root {
    --page-bg: #e9e7e4;
    --card-top-light: #f4f4f4;
    --card-top-mid: #cfcfcf;
    --skyline: #c4c4c4;
    --band-dark: #262626;
    --panel-dark: #3a3a3a;
    --accent-green: #5fd12f;
    --text-light: #d4d4d4;
    --text-muted: #bdbdbd;
    --logo-ink: #2e2e2e;
  }
  * { box-sizing: border-box; margin: 0; padding: 0; }
  html, body {
    width: 1200px; height: 800px; overflow: hidden;
    background: var(--page-bg);
    font-family: "Source Sans 3", "Source Sans Pro", sans-serif;
  }
  .business-card {
    position: absolute; left: 180px; top: 160px;
    width: 840px; height: 480px;
    background: radial-gradient(ellipse at 60% 20%, var(--card-top-light) 0%, var(--card-top-mid) 100%);
    overflow: hidden;
    box-shadow: 0 10px 30px rgba(0,0,0,0.18);
  }
  .skyline-backdrop {
    position: absolute; left: 0; top: 150px; width: 100%; height: 100px;
    background: linear-gradient(to bottom, rgba(196,196,196,0) 0%, var(--skyline) 100%);
    opacity: 0.7;
  }
  .brand-mark {
    position: absolute; left: 330px; top: 78px;
    display: flex; align-items: center; gap: 14px;
  }
  .brand-square { width: 26px; height: 26px; background: var(--accent-green); }
  .brand-name {
    font-size: 36px; font-weight: 600; letter-spacing: 2px; color: var(--logo-ink);
    white-space: nowrap;
  }
  .name-band {
    position: absolute; left: 0; top: 250px; width: 100%; height: 64px;
    background: var(--band-dark);
  }
  .holder-name {
    position: absolute; left: 40px; top: 11px;
    font-size: 34px; font-weight: 400; color: var(--accent-green);
    text-transform: uppercase; letter-spacing: 0.5px; white-space: nowrap;
  }
  .holder-title {
    position: absolute; left: 440px; top: 17px;
    font-size: 24px; color: var(--text-light); text-transform: uppercase;
    white-space: nowrap;
  }
  .contact-panel {
    position: absolute; left: 0; top: 314px; width: 100%; height: 166px;
    background: var(--panel-dark);
  }
  .contact-list { position: absolute; top: 24px; list-style: none; }
  .contact-list.phones { left: 40px; }
  .contact-list.details { left: 440px; right: 24px; }
  .contact-list li {
    display: flex; align-items: center; gap: 14px;
    height: 38px; font-size: 21px; color: var(--text-muted);
    white-space: nowrap;
  }
  .contact-list .no-icon { padding-left: 36px; }
  .contact-icon { width: 22px; height: 22px; flex: none; }
  .contact-icon * { fill: none; stroke: var(--accent-green); stroke-width: 2; }
</style>
</head>
<body>
  <div class="business-card">
    <div class="skyline-backdrop" role="img" aria-label="Faint city skyline silhouette behind the card top"></div>

    <div class="brand-mark">
      <span class="brand-square"></span>
      <span class="brand-name">BROCK CONSTRUCTION</span>
    </div>

    <div class="name-band">
      <div class="holder-name">Warren Pelkey</div>
      <div class="holder-title">Contractor</div>
    </div>

    <div class="contact-panel">
      <ul class="contact-list phones">
        <li>
          <svg class="contact-icon" viewBox="0 0 22 22" aria-label="Mobile"><rect x="6" y="2" width="10" height="18" rx="2"/><line x1="9" y1="17" x2="13" y2="17"/></svg>
          (415) 736-4052
        </li>
        <li>
          <svg class="contact-icon" viewBox="0 0 22 22" aria-label="Phone"><circle cx="11" cy="11" r="9"/><path d="M8 7c0 5 2 7 7 8l1-2-2-1-1 1c-2-1-3-2-3-4l1-1-1-2z"/></svg>
          (650) 514-2087
        </li>
        <li>
          <svg class="contact-icon" viewBox="0 0 22 22" aria-label="Fax"><rect x="3" y="3" width="16" height="16"/><rect x="6" y="6" width="10" height="5"/><line x1="6" y1="15" x2="16" y2="15"/></svg>
          (650) 514-2088
        </li>
      </ul>

      <ul class="contact-list details">
        <li>
          <svg class="contact-icon" viewBox="0 0 22 22" aria-label="Email"><circle cx="11" cy="11" r="9"/><rect x="6" y="8" width="10" height="7"/><path d="M6 8l5 4 5-4"/></svg>
          brock@brockconstruction.example
        </li>
        <li>
          <svg class="contact-icon" viewBox="0 0 22 22" aria-label="Address"><path d="M11 20s-6-6-6-11a6 6 0 0 1 12 0c0 5-6 11-6 11z"/><circle cx="11" cy="9" r="2"/></svg>
          Llc 514387, 3148 Larkspur Row
        </li>
        <li class="no-icon">San Bruno, California 94071</li>
      </ul>
    </div>
  </div>
</body>
</html>
```